Letter head / email signature/ contract document templates

We need a professional email signature and letterhead designed for our established carpentry and maintenance company. Our Logo (attached) was originally designed 6 years ago by design guru and we love it, looking for something to compliment it ( not a home job)

```html
<!DOCTYPE html>
<html lang="en">
<head>
<meta charset="utf-8">
<title>Harbourline Stationery</title>
<link href="https://fonts.googleapis.com/css2?family=Lato:wght@400;700&family=Arimo:wght@400&display=swap" rel="stylesheet">
<style>
:root{
  --backdrop:#8b8b8d;
  --paper:#f1f1f2;
  --ink:#3a3a3d;
  --muted:#55555a;
  --red:#c8102e;
  --dark-a:#5a5a5e;
  --dark-b:#28282b;
  --white:#ffffff;
}
*{margin:0;padding:0;box-sizing:border-box}
html,body{width:1200px;height:858px;overflow:hidden}
body{background:var(--backdrop);position:relative;font-family:'Lato',sans-serif;color:var(--ink)}
.sheet{position:absolute;background:var(--paper);overflow:hidden;box-shadow:0 2px 6px rgba(0,0,0,.25)}
.abs{position:absolute}
.brand{position:absolute;font-family:'Lato',sans-serif;font-weight:700;color:var(--ink);display:flex;align-items:center;gap:6px;white-space:nowrap}
.brand .dot{display:inline-block;background:var(--red)}
.icon{width:7px;height:7px;fill:var(--red);flex:none}
.dark .icon{fill:var(--white)}
.row{display:flex;align-items:center;gap:5px;white-space:nowrap}
.vrule{position:absolute;width:1px;background:#9a9a9e}
.redline{position:absolute;height:3px;background:var(--red)}
.band{position:absolute;background:linear-gradient(90deg,var(--dark-a),var(--dark-b))}
.site{position:absolute;color:var(--white);font-size:8.5px;letter-spacing:1.6px;text-align:center}

/* letterhead */
.letterhead{left:90px;top:73px;width:507px;height:712px}
.letterhead .company{left:187px;top:61px;font-size:8.4px;line-height:10.3px;color:var(--muted)}
.letterhead .company .name{color:var(--red)}
.letterhead .contacts{left:348px;top:63px;font-size:8.4px;line-height:10.4px;color:var(--muted)}
.letter{position:absolute;left:38px;top:178px;width:433px;font-family:'Arimo',sans-serif;color:var(--muted)}
.letter .salutation{font-size:12px;margin-bottom:19px}
.letter p{font-size:7.3px;line-height:10.8px;text-align:justify;margin-bottom:10.5px}
.letter .closing{margin-top:17px}
.signature{position:absolute;left:35px;top:476px;width:147px;height:42px;background:linear-gradient(90deg,rgba(60,60,64,.18),rgba(60,60,64,.08))}

/* card vertical */
.card-v{left:631px;top:215px;width:190px;height:258px}
.card-v .dark{position:absolute;left:0;top:106px;width:190px;height:152px}
.person{position:absolute;color:var(--white)}
.person .pname{font-size:13.5px;font-weight:700;line-height:15px}
.person .role{font-size:9px;line-height:11px;margin-bottom:8px}
.person .info{font-size:9px;line-height:11.2px}
.person .gap{height:6px}

/* card horizontal */
.card-h{left:631px;top:502px;width:402px;height:148px}
.card-h .dark{position:absolute;left:197px;top:0;width:205px;height:148px}

/* email signature */
.signoff{left:629px;top:677px;width:515px;height:108px}
.signoff .who{left:208px;top:33px}
.signoff .who .pname{font-size:13.5px;font-weight:700;color:var(--red);line-height:15px}
.signoff .who .role{font-size:9px;color:var(--muted)}
.signoff .contacts{left:341px;top:16px;font-size:9px;line-height:11.2px;color:var(--muted)}
</style>
</head>
<body>

<svg width="0" height="0" style="position:absolute" aria-hidden="true">
  <symbol id="i-phone" viewBox="0 0 10 10"><path d="M2 0.5l2 2-1 1.2c.6 1.3 1.6 2.3 2.9 2.9l1.2-1 2 2-1.3 1.9C4.4 9 1 5.6.5 1.8z"/></symbol>
  <symbol id="i-mobile" viewBox="0 0 10 10"><path d="M2.5 0h5v10h-5zM3.6 1v7.4h2.8V1z"/></symbol>
  <symbol id="i-mail" viewBox="0 0 10 10"><path d="M0 2h10v6.5H0zM1 3l4 3 4-3v-.1H1z"/></symbol>
  <symbol id="i-pin" viewBox="0 0 10 10"><path d="M5 0a3.6 3.6 0 0 1 3.6 3.6C8.6 6.3 5 10 5 10S1.4 6.3 1.4 3.6A3.6 3.6 0 0 1 5 0zm0 2.1a1.5 1.5 0 1 0 0 3 1.5 1.5 0 0 0 0-3z"/></symbol>
  <symbol id="i-globe" viewBox="0 0 10 10"><path d="M5 0a5 5 0 1 1 0 10A5 5 0 0 1 5 0zm-1 2.3L2 3.5l1 2 1.6.6-.3 2 1.2.8 1.4-2.4-1.4-1.6 1.6-1.3-.4-1.5z"/></symbol>
</svg>

<!-- Letterhead -->
<section class="sheet letterhead">
  <div class="brand" style="left:36px;top:59px;font-size:18px"><span class="dot" style="width:9px;height:9px"></span>Harbourline</div>
  <div class="vrule" style="left:167px;top:60px;height:33px"></div>
  <div class="abs company">
    <div class="name">Harbourline Carpentry &amp; Maintenance</div>
    <div>4120 Juniper Court</div>
    <div>Fairview, Oregon 97024</div>
  </div>
  <div class="vrule" style="left:323px;top:60px;height:33px"></div>
  <div class="abs contacts">
    <div class="row"><svg class="icon"><use href="#i-phone"/></svg>555-204-7781</div>
    <div class="row"><svg class="icon"><use href="#i-mobile"/></svg>555-318-6642</div>
    <div class="row"><svg class="icon"><use href="#i-mail"/></svg>info@harbourlinerepair.com</div>
  </div>

  <div class="letter">
    <div class="salutation">Dear Mr. Calder,</div>
    <p>Lorem ipsum dolor sit amet, consectetur adipiscing elit. Donec orci purus, luctus vitae dignissim eu, iaculis sed purus. Vivamus faucibus, ipsum nec aliquet viverra, leo mauris condimentum ligula, sit amet sagittis enim ligula quis arcu. Nam egestas tortor id nisi porttitor mattis. In tortor ante, ultricies in suscipit a, tempus non massa. Vivamus et auctor mi. Fusce vel massa nulla. Phasellus nec eros mauris, et scelerisque orci.</p>
    <p>Donec malesuada orci vitae nulla accumsan porta a id massa. Quisque accumsan iaculis magna sit amet fringilla. Maecenas consequat, magna eget tincidunt semper, odio nibh rutrum mi, id feugiat ante nisi eu risus. Vestibulum nunc orci, rhoncus a placerat in, ultricies in mi. Cras mattis varius eros, vel fringilla nisi suscipit eget. Quisque scelerisque sagittis nulla at porttitor.</p>
    <p>Sed id augue vitae urna euismod commodo aliquet a quam. Pellentesque arcu velit, cursus et malesuada ut, consequat et diam. Nullam erat sem, rhoncus id ullamcorper vitae, rhoncus et arcu. In ultricies ultricies nulla, ut rutrum nisi iaculis at. Donec eu magna a metus ornare faucibus. Fusce aliquet faucibus ultricies. Morbi semper, est id tincidunt gravida, sem arcu adipiscing lacus, ac bibendum nulla leo eu purus. Quisque nec diam sed risus consectetur a ccumsan quis quis nibh. Vestibulum id purus lorem.</p>
    <p>It is a long established fact that a reader will be distracted by the readable content of a page when looking at its layout. The point of using Lorem Ipsum is that it has a more-or-less normal distribution of letters, as opposed to using 'Content here, content here', making it look like readable English. Many desktop publishing packages</p>
    <p>ada ut, consequat et diam. Nullam erat sem, rhoncus id ullamcorper vitae, rhoncus et arcu. In ultricies ultricies nulla, ut rutrum nisi iaculis at. Donec eu magna a metus ornare faucibus. Fusce aliquet faucibus ultricies. Morbi semper,</p>
    <p class="closing">Sincerely,</p>
  </div>
  <div class="signature" role="img" aria-label="Handwritten signature"></div>

  <div class="redline" style="left:0;top:685px;width:507px"></div>
  <div class="band" style="left:0;top:689px;width:507px;height:23px"></div>
  <div class="site" style="left:0;top:695px;width:527px">www.harbourlinerepair.com</div>
</section>

<!-- Business card, portrait -->
<section class="sheet card-v">
  <div class="brand" style="left:25px;top:50px;font-size:19px"><span class="dot" style="width:9px;height:9px"></span>Harbourline</div>
  <div class="redline" style="left:14px;top:100px;width:176px"></div>
  <div class="band dark" style="top:104px;height:154px"></div>
  <div class="person" style="left:25px;top:126px">
    <div class="pname">Daniel Reeve</div>
    <div class="role">President</div>
    <div class="info">
      <div class="row"><svg class="icon"><use href="#i-pin"/></svg>4120 Juniper Court</div>
      <div style="padding-left:12px">Fairview, Oregon 97024</div>
      <div class="gap"></div>
      <div class="row"><svg class="icon"><use href="#i-phone"/></svg>555-204-7781</div>
      <div class="row"><svg class="icon"><use href="#i-mobile"/></svg>555-318-6642</div>
      <div class="row"><svg class="icon"><use href="#i-mail"/></svg>info@harbourlinerepair.com</div>
      <div class="row"><svg class="icon"><use href="#i-globe"/></svg>harbourlinerepair.com</div>
    </div>
  </div>
</section>

<!-- Business card, landscape -->
<section class="sheet card-h">
  <div class="brand" style="left:43px;top:62px;font-size:19px"><span class="dot" style="width:9px;height:9px"></span>Harbourline</div>
  <div class="abs" style="left:193px;top:14px;width:3px;height:134px;background:var(--red)"></div>
  <div class="band dark"></div>
  <div class="person" style="left:223px;top:22px">
    <div class="pname">Daniel Reeve</div>
    <div class="role">President</div>
    <div class="info">
      <div>4120 Juniper Court</div>
      <div>Fairview, Oregon 97024</div>
      <div class="gap"></div>
      <div class="row"><svg class="icon"><use href="#i-phone"/></svg>555-204-7781</div>
      <div class="row"><svg class="icon"><use href="#i-mobile"/></svg>555-318-6642</div>
      <div class="row"><svg class="icon"><use href="#i-mail"/></svg>info@harbourlinerepair.com</div>
      <div class="row"><svg class="icon"><use href="#i-globe"/></svg>harbourlinerepair.com</div>
    </div>
  </div>
</section>

<!-- Email signature -->
<section class="sheet signoff">
  <div class="brand" style="left:37px;top:38px;font-size:18px"><span class="dot" style="width:9px;height:9px"></span>Harbourline</div>
  <div class="vrule" style="left:182px;top:20px;height:53px"></div>
  <div class="abs who">
    <div class="pname">Daniel Reeve</div>
    <div class="role">President</div>
  </div>
  <div class="vrule" style="left:318px;top:20px;height:53px"></div>
  <div class="abs contacts">
    <div class="row"><svg class="icon"><use href="#i-pin"/></svg>4120 Juniper Court</div>
    <div style="padding-left:12px">Fairview, Oregon 97024</div>
    <div style="height:3px"></div>
    <div class="row"><svg class="icon"><use href="#i-phone"/></svg>555-204-7781</div>
    <div class="row"><svg class="icon"><use href="#i-mobile"/></svg>555-318-6642</div>
    <div class="row"><svg class="icon"><use href="#i-mail"/></svg>info@harbourlinerepair.com</div>
  </div>
  <div class="redline" style="left:0;top:86px;width:515px"></div>
  <div class="band" style="left:0;top:90px;width:515px;height:18px"></div>
  <div class="site" style="left:0;top:94px;width:531px">www.harbourlinerepair.com</div>
</section>

</body>
</html>
```